Dusty Spur Outfitters Home Page

I need a logo and page design for my home page, maybe some background color suggestions to go with it. I want the logo to project "vintage" and "western wear" but not be your typical trite western saddle and gun type thing.
http://www.dustyspuroutfitters.example/store/cart.php
Not looking for page coding just logo and other design elements to lay in over the site's template to make it "pop"
Reason: Have to finalize the design.
Target Market(s)
My customers are 70/30 men to women.
Industry/Entity Type
Gun

```html
<!DOCTYPE html>
<html lang="en">
<head>
<meta charset="utf-8">
<title>Dusty Spur Outfitters</title>
<link rel="stylesheet" href="https://fonts.googleapis.com/css2?family=Rye&family=Oswald:wght@500&family=Lato:wght@400;700&family=Damion&display=swap">
<style>
  :root {
    --sand: #d9cdb3;
    --cream: #eee3c6;
    --teal: #5c9ea3;
    --teal-deep: #3f8b91;
    --charcoal: #2b2a28;
    --ink: #26231f;
    --muted-script: #8b857a;
    --sky: #9fc8e3;
    --sky-deep: #6fa4c9;
  }
  * { margin: 0; padding: 0; box-sizing: border-box; }
  html, body { width: 1200px; height: 664px; overflow: hidden; }
  body { position: relative; background: var(--teal); font-family: "Lato", sans-serif; color: var(--ink); }
  .abs { position: absolute; }

  .utility-bar { left: 0; top: 0; width: 1200px; height: 28px; background: var(--sand); border-bottom: 7px solid var(--teal-deep); box-sizing: content-box; }
  .utility-bar a { position: absolute; top: 5px; font-family: "Oswald", sans-serif; font-size: 13.5px; color: var(--ink); text-decoration: none; letter-spacing: 0.2px; }

  .masthead { left: 0; top: 35px; width: 1200px; height: 111px; background: linear-gradient(180deg, #2e2d2b, #232220); }
  .brand-name { left: 39px; top: 66px; width: 270px; font-family: "Rye", serif; font-size: 21px; line-height: 1.2; color: var(--cream); text-align: center; }
  .tagline { left: 330px; top: 61px; width: 608px; font-family: "Damion", cursive; font-size: 23px; line-height: 29px; color: var(--muted-script); text-align: right; }
  .field { background: var(--cream); border-radius: 11px; font-family: "Lato", sans-serif; font-weight: 700; font-size: 12px; padding: 3px 11px; }
  .go { font-family: "Lato", sans-serif; font-weight: 700; font-size: 12px; color: #a9c7c4; }

  .side-title { font-family: "Rye", serif; color: #3a3631; text-shadow: 1px 1px 0 var(--cream); }
  .side-list { list-style: none; font-size: 11px; font-weight: 700; line-height: 13px; color: var(--ink); }

  .banner { left: 245px; top: 153px; width: 696px; height: 279px; border: 4px solid var(--cream); box-shadow: 1px 2px 4px rgba(0,0,0,0.35); }
  .banner-photo { width: 100%; height: 100%; background: linear-gradient(180deg, #bcc2c6 0%, var(--sky) 45%, var(--sky-deep) 100%); }
  .banner-caption { right: 10px; bottom: 4px; font-family: "Rye", serif; font-size: 26px; color: var(--cream); text-shadow: 1px 2px 2px rgba(0,0,0,0.5); }
  .slide-dot { top: 455px; width: 8px; height: 8px; border-radius: 50%; background: var(--charcoal); border: 1px solid var(--charcoal); }
  .slide-dot.active { background: var(--cream); border: 2px solid var(--charcoal); }

  .section-title { left: 248px; top: 488px; font-family: "Rye", serif; font-size: 28px; color: var(--cream); text-shadow: 1px 2px 2px rgba(0,0,0,0.45); }
  .product-card { top: 550px; width: 131px; height: 130px; border: 3px solid var(--cream); box-shadow: 1px 1px 3px rgba(0,0,0,0.3); }
  .product-photo { width: 100%; height: 100%; }

  .cart-title { left: 982px; top: 157px; width: 178px; text-align: center; font-family: "Rye", serif; font-size: 17px; color: var(--cream); text-shadow: 1px 1px 2px rgba(0,0,0,0.45); }
  .cart-box { left: 982px; top: 183px; width: 178px; height: 94px; background: var(--charcoal); border: 1px solid var(--cream); box-shadow: 1px 1px 3px rgba(0,0,0,0.3); }
  .cart-row { left: 9px; right: 9px; top: 8px; display: flex; justify-content: space-between; font-size: 12px; color: var(--cream); }
  .cart-row b { font-weight: 700; }
  .cart-button { left: 27px; width: 114px; height: 19px; background: var(--cream); border-radius: 10px; text-align: center; font-size: 12px; font-weight: 700; line-height: 19px; color: var(--ink); }
</style>
</head>
<body>
  <nav class="abs utility-bar" aria-label="Top navigation">
    <a style="left:38px">MEN'S WESTERN WEAR</a>
    <a style="left:169px">WOMEN'S WESTERN WEAR</a>
    <a style="left:318px">NEW ARRIVALS!</a>
    <a style="left:411px">BOOTS</a>
    <a style="left:823px">SIZING CHARTS</a>
    <a style="left:913px">HELP</a>
    <svg class="abs" style="left:1098px;top:6px" width="28" height="16" viewBox="0 0 28 16" aria-label="Account">
      <circle cx="6" cy="4" r="3.5" fill="#26231f"/><path d="M0 15c0-5 3-7 6-7s6 2 6 7z" fill="#26231f"/>
      <path d="M15 9l2.5 2.5L20 9" stroke="#26231f" stroke-width="1.6" fill="none"/>
    </svg>
    <svg class="abs" style="left:1130px;top:6px" width="32" height="17" viewBox="0 0 32 17" aria-label="Cart">
      <path d="M0 1h4l3 10h12l3-8H6" stroke="#26231f" stroke-width="2" fill="none"/>
      <circle cx="9" cy="14.5" r="1.7" fill="#26231f"/><circle cx="17" cy="14.5" r="1.7" fill="#26231f"/>
      <path d="M24 9l2.5 2.5L29 9" stroke="#26231f" stroke-width="1.6" fill="none"/>
    </svg>
  </nav>

  <header class="abs masthead" style="top:35px"></header>
  <div class="abs brand-name">Dusty Spur Outfitters</div>
  <p class="abs tagline">Internet's best selection and value for brand new Retro-Styled Vintage Western fashions for Men and Women</p>
  <div class="abs field" style="left:1000px;top:80px;width:113px;height:20px;line-height:14px;color:#3a3631">Search...</div>
  <div class="abs go" style="left:1121px;top:83px;color:#7d7a73">GO!</div>

  <aside>
    <div class="abs side-title" style="left:42px;top:172px;font-size:17px">LEAVE US A MESSAGE!</div>
    <div class="abs side-title" style="left:39px;top:216px;font-size:17px">Join our Newsletter!</div>
    <div class="abs field" style="left:38px;top:245px;width:116px;height:21px;line-height:15px;color:var(--teal);border:2px solid var(--charcoal)">Email</div>
    <div class="abs go" style="left:160px;top:249px">GO!</div>

    <div class="abs side-title" style="left:39px;top:303px;font-size:13px">CATEGORIES</div>
    <ul class="abs side-list" style="left:38px;top:327px">
      <li>Men's Western Wear</li><li>Women's Western Wear</li><li>Boots</li><li>Accessories</li>
      <li>Belts</li><li>Big and tall</li><li>Brand New Arrivals</li><li>CLEARANCE</li>
      <li>Handbags</li><li>Jackets</li><li>Jeans</li><li>Leather</li><li>ON Sale</li>
      <li>Pants</li><li>Short Sleeves</li><li>T-Shirts</li><li>Vests</li>
    </ul>

    <div class="abs side-title" style="left:39px;top:566px;font-size:13px">INFORMATION</div>
    <ul class="abs side-list" style="left:38px;top:590px">
      <li>About Us</li><li>Contact Us</li><li>Privacy Policy</li><li>Shipping and Returns</li><li>Sizing Charts</li>
    </ul>
  </aside>

  <main>
    <section class="abs banner">
      <div class="banner-photo" role="img" aria-label="Close-up of a light blue western shirt with embroidered yoke"></div>
      <div class="abs banner-caption">NEW ARRIVALS</div>
    </section>
    <span class="abs slide-dot active" style="left:578px"></span>
    <span class="abs slide-dot" style="left:597px"></span>

    <h2 class="abs section-title">FEATURED PRODUCTS</h2>
    <div class="abs product-card" style="left:261px"><div class="product-photo" role="img" aria-label="Man in a black embroidered western shirt" style="background:linear-gradient(180deg,#6ad3e6,#2c3436 70%)"></div></div>
    <div class="abs product-card" style="left:438px"><div class="product-photo" role="img" aria-label="Man in a cream shirt with sky blue yoke" style="background:linear-gradient(180deg,#a8d6ec,#e4dccb 75%)"></div></div>
    <div class="abs product-card" style="left:614px"><div class="product-photo" role="img" aria-label="Man in a black hat and burgundy vest" style="background:linear-gradient(180deg,#8fc3e4,#6a3a36 80%)"></div></div>
    <div class="abs product-card" style="left:790px"><div class="product-photo" role="img" aria-label="Man in a brown hat and patterned vest" style="background:linear-gradient(180deg,#a2cfe8,#86705c 80%)"></div></div>
  </main>

  <aside>
    <div class="abs cart-title">SHOPPING CART</div>
    <div class="abs cart-box">
      <div class="abs cart-row"><span>Subtotal:</span><b>$ 0.00</b></div>
      <div class="abs cart-button" style="top:31px">Update Cart</div>
      <div class="abs cart-button" style="top:58px">Checkout</div>
    </div>
  </aside>
</body>
</html>
```